Print materials for 3-star hotel

We are changing up our print materials (notepads, letterheads, key card jackets, small flyer for the room rates) We are a 3 star business hotel in the Philippines and have mainly used grey tones and clean, simple lines. See attached photos for logo and hotel interior photos.

Target Market(s)

Business

Contact Information for Business Card

Corvale Terrace Hotel
Lindwell Banca Avenue corner Tolenta St Cebu City 6000 Philippines
Tel: +63 32 481 7302
Mobile: +63 917 648 2095
www.corvaleterracehotel.example

Font styles to use
Serif
Sans Serif

Requirements
Must have
• Simple
• Readable font and font size
Nice to have
• Neutral colors, grey and taupes
Should not have
• No purples and bright blues

```html
<!DOCTYPE html>
<html lang="en">
<head>
<meta charset="utf-8">
<title>Corvale Terrace Hotel – Business Card</title>
<link rel="stylesheet" href="https://fonts.googleapis.com/css2?family=Montserrat:wght@400;500;700&display=swap">
<style>
  :root {
    --page-bg: #eeeeee;
    --card-white: #f9f9f9;
    --card-grey: #8c8c8c;
    --ink: #7a7a7a;
    --ink-strong: #6a6a6a;
    --ink-on-grey: #f2f2f2;
    --rule: #9a9a9a;
  }
  * { box-sizing: border-box; margin: 0; padding: 0; }
  html, body {
    width: 1200px; height: 1163px; overflow: hidden;
    background: var(--page-bg);
    font-family: "Montserrat", sans-serif;
  }
  .card {
    position: absolute; left: 150px;
    width: 900px; height: 514px;
    box-shadow: 0 6px 18px rgba(0,0,0,0.08);
  }
  .card-back { top: 45px; background: var(--card-grey); }
  .card-back .pattern-fill {
    position: absolute; inset: 0;
    background: linear-gradient(135deg, #909090, #878787);
  }
  .back-brand {
    position: absolute; left: 0; right: 0; top: 50%;
    transform: translateY(-50%);
    text-align: center;
    color: var(--ink-on-grey);
    font-weight: 400; font-size: 46px;
    letter-spacing: 0.22em; text-transform: uppercase;
  }
  .card-front { top: 604px; background: var(--card-white); }
  .person-name {
    position: absolute; left: 70px; top: 58px;
    font-weight: 700; font-size: 30px; color: var(--ink-strong);
  }
  .person-role {
    position: absolute; left: 70px; top: 100px;
    font-size: 17px; color: var(--ink);
  }
  .divider {
    position: absolute; left: 70px; top: 152px;
    width: 80px; height: 1px; background: var(--rule);
  }
  .contact-list {
    position: absolute; left: 70px; top: 186px;
    list-style: none; font-size: 19px; color: var(--ink);
  }
  .contact-list li { display: flex; align-items: center; height: 32px; }
  .contact-list svg { width: 18px; height: 18px; margin-right: 12px; flex: none; }
  .front-brand {
    position: absolute; right: 70px; top: 250px;
    display: flex; align-items: center; gap: 12px;
    font-weight: 700; font-size: 22px; color: var(--ink-strong);
  }
  .front-brand .brand-square { width: 16px; height: 16px; background: var(--ink-strong); }
  .address {
    position: absolute; right: 70px; top: 330px;
    text-align: right; font-size: 19px; line-height: 1.45; color: var(--ink);
    font-style: normal;
  }
  .address strong { font-weight: 700; color: var(--ink-strong); }
</style>
</head>
<body>
  <section class="card card-back">
    <div class="pattern-fill" role="img" aria-label="Subtle grey wave line pattern"></div>
    <div class="back-brand">Corvale Terrace Hotel</div>
  </section>

  <section class="card card-front">
    <h1 class="person-name">Adrian VELASCO</h1>
    <p class="person-role">Managing Director</p>
    <div class="divider"></div>
    <ul class="contact-list">
      <li><svg viewBox="0 0 18 18"><circle cx="9" cy="9" r="8" fill="none" stroke="#8a8a8a" stroke-width="1.3"/><path d="M6 5.5l1.6-.4.9 2-1 .8a5 5 0 0 0 2.6 2.6l.8-1 2 .9-.4 1.6c-3.6.3-6.8-2.9-6.5-6.5z" fill="#8a8a8a"/></svg>+63 32 481 7302</li>
      <li><svg viewBox="0 0 18 18"><circle cx="9" cy="9" r="8" fill="none" stroke="#8a8a8a" stroke-width="1.3"/><rect x="6.5" y="4.5" width="5" height="9" rx="1" fill="#8a8a8a"/></svg>+63 917 648 2095</li>
      <li><svg viewBox="0 0 18 18"><circle cx="9" cy="9" r="8" fill="none" stroke="#8a8a8a" stroke-width="1.3"/><rect x="5" y="6" width="8" height="6" fill="#8a8a8a"/></svg>+63 918 552 0764</li>
      <li><svg viewBox="0 0 18 18"><circle cx="9" cy="9" r="8" fill="none" stroke="#8a8a8a" stroke-width="1.3"/><rect x="5" y="6" width="8" height="6" fill="none" stroke="#8a8a8a"/><path d="M5 6l4 3 4-3" fill="none" stroke="#8a8a8a"/></svg>adrian@corvaleterracehotel.example</li>
      <li><svg viewBox="0 0 18 18"><circle cx="9" cy="9" r="8" fill="none" stroke="#8a8a8a" stroke-width="1.3"/><circle cx="9" cy="9" r="4" fill="none" stroke="#8a8a8a"/><path d="M5 9h8M9 5v8" stroke="#8a8a8a"/></svg>www.corvaleterracehotel.example</li>
    </ul>
    <div class="front-brand"><span class="brand-square"></span>Corvale Terrace Hotel</div>
    <address class="address">
      Lindwell Banca Avenue corner<br>
      Tolenta St, Cebu City<br>
      Cebu, 6000, <strong>Philippines</strong>
    </address>
  </section>
</body>
</html>
```